UI Redesign For Mobile Events iPhone App

We need a new UI design for our Social Events mobile app. Our app called Vessa is geared to help users find trending events in their local area. We show visual metrics on percent full and male female ratio and age group ratings. We want people to see whats going on at event before they get there through our app. Also we have a group chat portion to our app that we need included in the design. We would like to see a fresh, clean, and easy to use user interface that uses colors like, purple, blue and or hot pink.You may visit our website myvessa.example for more information about what our app is geared to do.
Updates

Target Market(s)

Our target market people that use social networks and attend social events ranging from ages 16-44.

Industry/Entity Type

Events

Requirements
Must have
• We would like to see an Example layout of all screens. (UPDATE: Please use our current background in your design, A PSD has been uploaded for you to grab the background. The Vessa Logo is NOT required to be included at the top of every screen)

-Profile Screen: Shows points earned, events attending, events created
-Event Listings Screen: Must have large image for event, visual metrics, date& time, location, attend button, invite friends button, Label for user who created the event
-Event Description Page: Shows everything as the event listing, has a description of the event, shows friends that are attending, points available
-Group Messaging Screen
-Slide Out Navigation Screen
-Notification Screen
-Ticket Screen
-Friends Activity Screen
-Friends Profile View: Shows events they've attended and points they've earned under their contact picture; invite button
-Sign-In Screen
-Register Screen

A way to label/categorize our different types of events:
-Nightlife
-Family
-Live Music & Concerts
-Restaurants
Group Chat Layout
Visual Meters for Percent Full, Male Female Ratio, Age Rating

```html
<!DOCTYPE html>
<html lang="en">
<head>
<meta charset="utf-8">
<title>Vessa app UI</title>
<link href="https://fonts.googleapis.com/css2?family=Open+Sans:wght@300;400;600&family=Poiret+One&family=Montserrat:wght@400&display=swap" rel="stylesheet">
<style>
:root{
  --bg:#2f3d58;
  --bg-light:#3e5478;
  --purple:#9654b6;
  --purple-dark:#6c3b8c;
  --purple-mid:#7c4f9f;
  --purple-pale:#e0cbeb;
  --blue:#00aeef;
  --blue-dark:#0a8fd0;
  --navy:#24324a;
  --white:#ffffff;
  --ink:#2b2b2b;
  --muted:#9a9aa8;
}
*{box-sizing:border-box;margin:0;padding:0}
html,body{width:1200px;height:900px;overflow:hidden}
body{
  position:relative;
  font-family:"Open Sans",Arial,sans-serif;
  background:radial-gradient(ellipse at 55% 45%,var(--bg-light) 0%,var(--bg) 70%);
  color:var(--white);
}
h1,h2,h3,p{font-weight:400}
.stripe{position:absolute;left:0;width:1200px;height:6px;
  background:linear-gradient(90deg,var(--purple) 0 25%,var(--blue) 25% 50%,var(--purple) 50% 75%,var(--blue) 75% 100%)}
.stripe.top{top:0}.stripe.bottom{bottom:0}
.card{position:absolute;border-radius:12px;overflow:hidden;box-shadow:0 4px 10px rgba(0,0,0,.35)}

/* brand */
.brand-card{left:55px;top:45px;width:270px;height:297px;background:var(--purple)}
.brand-card .upper{height:247px;background:var(--purple-mid);position:relative}
.brand-mark{position:absolute;left:20px;top:60px;display:flex;align-items:center;gap:16px}
.brand-mark .dot{width:70px;height:70px;border-radius:50%;background:#5c5fa8}
.brand-mark .name{font-weight:300;font-size:40px;letter-spacing:2px;color:var(--white)}
.tagline{position:absolute;top:166px;width:100%;text-align:center;font-size:25px;line-height:32px;letter-spacing:.5px}

/* login */
.login-card{left:55px;top:386px;width:265px;height:206px;background:var(--purple)}
.field{position:absolute;left:17px;width:230px;height:50px;background:var(--white);border-radius:6px;display:flex;align-items:center}
.field svg{margin:0 14px 0 16px}
.field span{border-left:1px solid #ddd;padding-left:13px;color:var(--muted);font-size:15px;line-height:28px}
.field.user{top:14px}.field.pass{top:76px}
.slide-band{position:absolute;left:0;top:144px;width:100%;height:62px;background:var(--blue)}
.slide-track{position:absolute;left:17px;top:13px;width:230px;height:36px;background:var(--blue-dark);border-radius:5px;display:flex;align-items:center}
.slide-knob{width:52px;height:36px;background:var(--white);border-radius:5px;display:flex;align-items:center;justify-content:center}
.slide-track span{margin-left:15px;font-size:15px;color:#bfe6f8}

/* nav */
.nav{left:375px;top:43px;width:772px;height:74px;border-radius:8px;display:flex;background:var(--purple)}
.nav-item{flex:1;display:flex;flex-direction:column;align-items:center;justify-content:flex-end;padding-bottom:6px;font-size:17px;border-right:1px solid rgba(255,255,255,.25);gap:2px}
.nav-item:last-child{border:none;background:var(--purple-dark);justify-content:center;padding:0}

/* event */
.event-card{left:375px;top:165px;width:450px;height:295px;background:var(--white)}
.event-card .head{height:220px;background:var(--purple);position:relative}
.event-photo{position:absolute;left:15px;top:18px;width:425px;height:170px;
  background:radial-gradient(ellipse at 60% 20%,#f6c46a 0%,#d9772a 30%,#5a2410 65%,#120806 100%)}
.event-title{position:absolute;left:16px;top:193px;font-size:19px;letter-spacing:1.2px;font-weight:400}
.meter{position:absolute;left:0;display:flex;align-items:center;font-size:15px}
.meter label{width:102px;text-align:right;padding-right:10px}
.meter.going{top:235px;color:#444}.meter.going label{width:82px;margin-right:20px}
.meter.not{top:260px;color:var(--muted)}
.track{height:14px;border-radius:3px}
.going .track{width:310px;background:var(--purple-pale)}
.going .fill{width:225px;height:14px;background:var(--purple);border-radius:3px}
.not .track{width:150px;background:var(--blue)}

/* chat */
.chat-card{left:375px;top:508px;width:450px;height:206px;background:var(--purple)}
.chat-title{position:absolute;left:251px;top:18px;font-family:"Montserrat",sans-serif;font-weight:400;font-size:27px;letter-spacing:2px}
.avatar{position:absolute;border-radius:4px;border:2px solid #ddd}
.avatar.a1{left:35px;top:52px;width:50px;height:52px;background:#6d6d6d}
.avatar.a2{left:370px;top:122px;width:52px;height:46px;background:#a4765f}
.bubble{position:absolute;height:32px;border-radius:16px;font-size:17px;line-height:32px;padding:0 8px;white-space:nowrap}
.bubble.in{left:104px;top:64px;background:linear-gradient(#ececec,#b9b9b9);color:var(--ink)}
.bubble.out{left:43px;top:132px;background:linear-gradient(#b8a4f5,#8a6ce0);color:var(--white);border:1px solid #6e5bc7}

/* categories */
.category-card{left:876px;top:164px;width:270px;height:242px;background:var(--purple)}
.category{height:60px;display:flex;align-items:center;font-size:15px}
.category svg{width:50px;margin:0 12px 0 10px}
.category.active{background:var(--blue);height:62px}

/* stats */
.stats-card{left:870px;top:418px;width:267px;height:295px;background:var(--white)}
.stats-card .head{height:212px;background:var(--purple);position:relative}
.ring-label{position:absolute;line-height:1.2}
.ring-label.m{left:46px;top:52px;font-size:20px}
.ring-label.f{left:158px;top:136px;font-size:15px}
.stats-card .foot{position:relative;height:83px;color:var(--ink);font-size:14px}
.foot .lbl{position:absolute}
.bar{position:absolute;top:12px;width:19px;height:58px}
.bar i{position:absolute;bottom:0;left:0;width:100%}

/* share */
.share{position:absolute;left:873px;top:787px;width:267px;height:62px;border-radius:8px;overflow:hidden;box-shadow:0 4px 10px rgba(0,0,0,.35)}
.share-half{position:absolute;top:0;height:62px}
.share-half.left{left:0;width:133px;background:var(--blue)}
.share-half.right{left:133px;width:134px;background:var(--blue-dark)}
.share-label{position:absolute;top:0;line-height:62px;font-size:16px;font-weight:600;text-align:center}
.share-label.left{left:0;width:108px}
.share-label.right{left:158px;width:109px}
.share-knob{position:absolute;left:108px;top:6px;width:50px;height:50px;border-radius:50%;background:var(--navy);display:flex;align-items:center;justify-content:center}

.showcase-title{position:absolute;left:72px;top:718px;font-family:"Poiret One",sans-serif;font-size:44px;font-weight:400}
</style>
</head>
<body>
<div class="stripe top"></div>

<section class="card brand-card">
  <div class="upper">
    <div class="brand-mark"><span class="dot"></span><span class="name">VESSA</span></div>
    <p class="tagline">events at your<br>fingertips !</p>
  </div>
</section>

<section class="card login-card">
  <div class="field user">
    <svg width="24" height="20" viewBox="0 0 24 20"><circle cx="12" cy="6" r="5" fill="none" stroke="#cdb3dd" stroke-width="2"/><path d="M2 19c1-6 19-6 20 0z" fill="none" stroke="#cdb3dd" stroke-width="2"/></svg>
    <span>Username</span></div>
  <div class="field pass">
    <svg width="24" height="22" viewBox="0 0 24 22"><path d="M7 9V6a5 5 0 0 1 10 0v3" fill="none" stroke="#cdb3dd" stroke-width="2"/><rect x="4" y="9" width="16" height="12" rx="2" fill="none" stroke="#cdb3dd" stroke-width="2"/></svg>
    <span>Password</span></div>
  <div class="slide-band">
    <div class="slide-track">
      <div class="slide-knob"><svg width="20" height="14" viewBox="0 0 20 14"><path d="M1 7h16M11 1l6 6-6 6" fill="none" stroke="#00aeef" stroke-width="2.5"/></svg></div>
      <span>Slide to login</span>
    </div>
  </div>
</section>

<nav class="card nav">
  <div class="nav-item"><svg width="40" height="34" viewBox="0 0 40 34"><circle cx="20" cy="10" r="9" fill="#fff"/><path d="M3 34c2-13 32-13 34 0z" fill="#fff"/></svg>profile</div>
  <div class="nav-item"><svg width="14" height="14" viewBox="0 0 14 14"><circle cx="7" cy="7" r="6" fill="none" stroke="#fff" stroke-width="1.5"/></svg>my vessa</div>
  <div class="nav-item"><svg width="40" height="34" viewBox="0 0 40 34"><rect x="2" y="5" width="36" height="28" rx="2" fill="none" stroke="#fff" stroke-width="2.5"/><rect x="2" y="5" width="36" height="7" fill="#fff"/><path d="M8 1v8M32 1v8M2 19h36M2 26h36M11 12v21M20 12v21M29 12v21" stroke="#fff" stroke-width="2"/></svg>events</div>
  <div class="nav-item"><svg width="50" height="36" viewBox="0 0 50 36"><path d="M6 22 30 2l4 4a4 4 0 0 0 6 6l4 4-24 20-4-4a4 4 0 0 0-6-6z" fill="#fff"/></svg>tickets</div>
  <div class="nav-item"><svg width="38" height="38" viewBox="0 0 38 38"><g fill="#fff"><circle cx="19" cy="19" r="12"/><rect x="15" y="1" width="8" height="36" rx="1"/><rect x="15" y="1" width="8" height="36" rx="1" transform="rotate(45 19 19)"/><rect x="15" y="1" width="8" height="36" rx="1" transform="rotate(90 19 19)"/><rect x="15" y="1" width="8" height="36" rx="1" transform="rotate(135 19 19)"/></g><circle cx="19" cy="19" r="5" fill="#6c3b8c"/></svg></div>
</nav>

<section class="card event-card">
  <div class="head">
    <div class="event-photo" role="img" aria-label="Concert crowd with raised hands under warm stage lights"></div>
    <h2 class="event-title">Marlo Venn Live ,Vancouver</h2>
  </div>
  <div class="meter going"><label>Going</label><div class="track"><div class="fill"></div></div></div>
  <div class="meter not"><label>Not going</label><div class="track"></div></div>
</section>

<section class="card chat-card">
  <h3 class="chat-title">chats</h3>
  <div class="avatar a1" role="img" aria-label="Chat member photo"></div>
  <p class="bubble in">Do you know about the new event?</p>
  <p class="bubble out">Yeah, just checked it out in Vessa</p>
  <div class="avatar a2" role="img" aria-label="Chat member photo"></div>
</section>

<section class="card category-card">
  <div class="category"><svg height="36" viewBox="0 0 50 36"><path d="M16 2v12M20 2v12M24 2v12M16 14h8M20 14v20" stroke="#fff" stroke-width="3" fill="none"/><path d="M32 2c6 2 6 14 0 16v16" stroke="#fff" stroke-width="4" fill="none"/></svg>Restaurants</div>
  <div class="category"><svg height="40" viewBox="0 0 50 40"><path d="M8 8h30L23 24z" fill="#fff"/><path d="M23 24v12M14 37h18" stroke="#fff" stroke-width="3"/><circle cx="40" cy="32" r="3" fill="#fff"/></svg>Nightlife</div>
  <div class="category active"><svg height="40" viewBox="0 0 50 40"><circle cx="34" cy="11" r="9" fill="none" stroke="#fff" stroke-width="3"/><path d="M27 17 8 36" stroke="#fff" stroke-width="5" stroke-linecap="round"/></svg>Live concerts</div>
  <div class="category"><svg height="36" viewBox="0 0 60 36"><g fill="#fff"><circle cx="10" cy="6" r="4"/><rect x="6" y="11" width="8" height="24"/><circle cx="26" cy="5" r="4"/><rect x="22" y="10" width="8" height="25"/><circle cx="40" cy="12" r="3"/><rect x="37" y="16" width="6" height="19"/><circle cx="52" cy="14" r="3"/><rect x="49" y="18" width="6" height="17"/></g></svg>Family</div>
</section>

<section class="card stats-card">
  <div class="head">
    <svg width="267" height="212" viewBox="0 0 267 212" style="position:absolute;left:0;top:0">
      <circle cx="90" cy="80" r="62" fill="none" stroke="#6c3b8c" stroke-width="2" opacity=".6"/>
      <path d="M90 18a62 62 0 1 1-2 124" fill="none" stroke="#6c3b8c" stroke-width="18"/>
      <circle cx="196" cy="159" r="46" fill="none" stroke="#00aeef" stroke-width="2"/>
      <path d="M196 113a46 46 0 0 1 0 92" fill="none" stroke="#00aeef" stroke-width="12"/>
    </svg>
    <p class="ring-label m">64%<br>MALES</p>
    <p class="ring-label f">50%<br>FEMALES</p>
  </div>
  <div class="foot">
    <span class="lbl" style="left:35px;top:10px">FULL</span>
    <span class="lbl" style="left:28px;top:57px">EMPTY</span>
    <div class="bar" style="left:90px;background:#eadcf1"><i style="height:24px;background:var(--purple)"></i></div>
    <div class="bar" style="left:124px;background:#d6eef9"><i style="height:52px;background:var(--blue)"></i></div>
    <div class="bar" style="left:158px;background:#eadcf1"><i style="height:30px;background:var(--purple)"></i></div>
    <span class="lbl" style="left:187px;top:8px">44 YEARS</span>
    <span class="lbl" style="left:187px;top:58px">16 YEARS</span>
  </div>
</section>

<h1 class="showcase-title">Vessa</h1>

<div class="share">
  <div class="share-half left"></div>
  <div class="share-half right"></div>
  <span class="share-label left">Chirper</span>
  <span class="share-label right">Friendbook</span>
  <span class="share-knob"><svg width="26" height="26" viewBox="0 0 26 26"><circle cx="13" cy="13" r="12" fill="#fff"/><g fill="#24324a"><circle cx="8" cy="13" r="2.5"/><circle cx="17" cy="8" r="2.5"/><circle cx="17" cy="18" r="2.5"/></g><path d="M8 13l9-5M8 13l9 5" stroke="#24324a" stroke-width="1.5"/></svg></span>
</div>

<div class="stripe bottom"></div>
</body>
</html>
```